Local Flower Farm Needs Business Card Design

I need business cards designed for a flower farm based in Eudora, Kansas.
Business Info:
We are a local cut flower farm located in Eudora, Kansas, founded by Corinne Haldwick. What started as a passion for agriculture and search for more joy in daily life has blossomed into a small business dedicated to providing the community with beautiful, fresh, and sustainable flowers. We specialize in local, seasonal blooms, ensuring that every petal reflects the care and dedication we pour into our craft. Our mission is to deliver the highest quality flowers directly to our customers through local farmers markets and to florists who share our commitment to sustainability. Join us in celebrating the beauty of nature, one bloom at a time!
Contact Details:
Corinne Haldwick
Owner
Phone 913-555-0147
Facebook: Rosalind Thorpe Gardens
Instagram: @RosalindThorpeGardens
Website: RosalindThorpeGardens.example
Target Market(s)
Wholesale to Florists and Direct to Consumer via Farmers Market
Industry/Entity Type
Florist, Farm
Contact Information for Business Card
Name, Contact Info, Logo
Look and feel
Each slider illustrates characteristics of the customer's brand and the style your logo design should communicate.

```html
<!DOCTYPE html>
<html lang="en">
<head>
<meta charset="utf-8">
<title>Rosalind Thorpe Gardens – Business Card</title>
<link href="https://fonts.googleapis.com/css2?family=Tinos:wght@400;700&display=swap" rel="stylesheet">
<style>
  :root {
    --page: #dde3e6;
    --card: #0b2830;
    --ink: #ffffff;
    --shadow: rgba(0, 0, 0, 0.28);
  }
  * { margin: 0; padding: 0; box-sizing: border-box; }
  html, body {
    width: 1200px; height: 960px; overflow: hidden;
    background: var(--page);
    font-family: "Tinos", "Times New Roman", serif;
    color: var(--ink);
  }
  .card {
    position: absolute;
    background: var(--card);
    box-shadow: 0 10px 22px var(--shadow);
  }
  .card--front { left: 246px; top: 58px; width: 709px; height: 406px; }
  .card--back  { left: 250px; top: 500px; width: 701px; height: 400px; }

  .brand-seal {
    position: absolute;
    width: 270px; height: 270px;
    border: 1px solid var(--ink);
    border-radius: 50%;
    display: flex; flex-direction: column;
    align-items: center; justify-content: center;
    text-align: center;
  }
  .card--front .brand-seal { left: 219px; top: 68px; }
  .card--back .brand-seal { left: 25px; top: 63px; }
  .brand-name {
    font-weight: 400;
    font-size: 30px;
    line-height: 1.15;
    letter-spacing: 0.12em;
    text-transform: uppercase;
    color: var(--ink);
  }

  .holder {
    position: absolute; right: 29px; top: 170px;
    text-align: right;
  }
  .holder-name {
    font-weight: 700; font-size: 34px; letter-spacing: 0.04em; line-height: 1.1;
  }
  .holder-role { font-size: 17px; letter-spacing: 0.05em; line-height: 1.2; }
  .accent-bar {
    position: absolute; right: 0; top: 177px;
    width: 17px; height: 47px; background: var(--ink);
  }

  .contact-list {
    position: absolute; right: 29px; top: 282px;
    list-style: none;
  }
  .contact-item {
    display: flex; align-items: center; justify-content: flex-end;
    height: 24px;
    font-size: 17px; letter-spacing: 0.05em;
  }
  .contact-icon {
    width: 17px; height: 17px; margin-left: 16px; flex: none;
  }
</style>
</head>
<body>
  <section class="card card--front">
    <div class="brand-seal">
      <span class="brand-name">Rosalind<br>Thorpe<br>Gardens</span>
    </div>
  </section>

  <section class="card card--back">
    <div class="brand-seal">
      <span class="brand-name">Rosalind<br>Thorpe<br>Gardens</span>
    </div>

    <div class="holder">
      <p class="holder-name">Corinne Haldwick</p>
      <p class="holder-role">Owner</p>
    </div>
    <div class="accent-bar"></div>

    <ul class="contact-list">
      <li class="contact-item">913-555-0147
        <svg class="contact-icon" viewBox="0 0 24 24" aria-hidden="true">
          <path fill="#fff" d="M6.6 10.8a15.1 15.1 0 0 0 6.6 6.6l2.2-2.2a1 1 0 0 1 1-.25 11.4 11.4 0 0 0 3.6.57 1 1 0 0 1 1 1V20a1 1 0 0 1-1 1A17 17 0 0 1 3 4a1 1 0 0 1 1-1h3.5a1 1 0 0 1 1 1c0 1.25.2 2.45.57 3.57a1 1 0 0 1-.25 1z"/>
        </svg>
      </li>
      <li class="contact-item">Rosalind Thorpe Gardens
        <svg class="contact-icon" viewBox="0 0 24 24" aria-hidden="true"><circle cx="12" cy="12" r="11" fill="#fff"/></svg>
      </li>
      <li class="contact-item">@RosalindThorpeGardens
        <svg class="contact-icon" viewBox="0 0 24 24" aria-hidden="true"><circle cx="12" cy="12" r="11" fill="#fff"/></svg>
      </li>
      <li class="contact-item">RosalindThorpeGardens.example
        <svg class="contact-icon" viewBox="0 0 24 24" aria-hidden="true">
          <g fill="none" stroke="#fff" stroke-width="1.8">
            <circle cx="12" cy="12" r="10"/>
            <ellipse cx="12" cy="12" rx="4.5" ry="10"/>
            <path d="M2 12h20M4 7h16M4 17h16"/>
          </g>
        </svg>
      </li>
    </ul>
  </section>
</body>
</html>
```